Verdanith Website Concept

We would like a one page website. Please refer to the attached files for more information.

Please reference file attachment version 1.1.

```html
<!DOCTYPE html>
<html lang="en">
<head>
<meta charset="utf-8">
<title>Verdanith Website Concept</title>
<link href="https://fonts.googleapis.com/css2?family=Open+Sans:ital,wght@0,400;0,600;0,700;1,600&display=swap" rel="stylesheet">
<style>
:root{
  --blue:#5b9bd0;
  --blue-dark:#4a87bd;
  --ink:#333;
  --muted:#9a9a9a;
  --line:#e3e3e3;
  --panel:#f4f4f4;
  --footer:#3b3b3b;
  --footer-deep:#2f2f2f;
  --footer-text:#a8a8a8;
  --white:#fff;
}
*{margin:0;padding:0;box-sizing:border-box}
html,body{width:1200px;height:1000px;overflow:hidden;background:var(--white)}
body{position:relative;font-family:"Open Sans",Arial,sans-serif;color:var(--ink)}
.abs{position:absolute}
.topbar{left:0;top:0;width:1200px;height:11px;background:var(--blue);color:var(--white);font-size:6px;line-height:11px}
.topbar span{position:absolute;top:0}
.topbar .dot{display:inline-block;width:6px;height:5px;background:var(--white);border-radius:1px;margin-right:6px;vertical-align:-1px}
.social-top{position:absolute;top:3px;width:6px;height:5px;background:var(--white);border-radius:1px}
.header{left:0;top:11px;width:1200px;height:47px;background:var(--white)}
.brand{left:210px;top:18px;display:flex;align-items:center;gap:6px}
.brand-mark{width:30px;height:20px;background:#2b4a66;border-radius:50%}
.brand-name{font-size:16px;font-weight:700;color:#2b4a66;letter-spacing:.5px}
.nav{top:31px;font-size:7.5px;color:#333}
.nav.active{color:var(--blue);border-left:2px solid var(--blue);padding-left:8px}
.hero{left:0;top:58px;width:1200px;height:155px;background:linear-gradient(90deg,#3f4a55 0%,#6f7a80 30%,#9c9f98 50%,#7f8583 70%,#b9b4a6 90%,#a9a294 100%)}
.hero-rule{left:0;top:213px;width:1200px;height:2px;background:var(--blue)}
.hero-title{left:206px;top:77px;font-size:17px;color:var(--white);white-space:nowrap}
.hero-tag{left:210px;height:17px;background:rgba(91,155,208,.85);color:var(--white);font-size:12.5px;line-height:17px;padding:0 7px}
.intro{left:209px;top:236px;width:807px;height:36px;background:var(--panel);border-left:3px solid var(--blue);border-right:3px solid #cfe0ee;text-align:center}
.intro h2{font-size:13px;font-weight:600;margin-top:6px}
.intro p{font-size:6.5px;color:var(--muted)}
.feature-icon{width:40px;height:15px;background:var(--blue);border-radius:50%}
.feature-icon::after{content:"";position:absolute;left:17px;top:5px;width:6px;height:5px;background:var(--white);border-radius:1px}
.feature h3{font-size:11px;font-weight:600;line-height:12px}
.feature p{font-size:6.8px;line-height:8px;color:var(--muted);width:200px;margin-top:3px}
.feature a{display:block;font-size:6.8px;color:var(--blue);margin-top:8px;text-decoration:none}
.section-title{font-size:11px;font-weight:600}
.section-rule{height:1px;background:var(--line)}
.section-link{font-size:6.5px;font-style:italic;font-weight:600}
.photo{height:72px}
.tabs{left:211px;top:597px;display:flex}
.tab{width:115px;height:12px;border:1px solid var(--line);border-bottom:none;font-size:7.5px;text-align:center;line-height:11px;color:#aaa;background:#fafafa}
.tab.on{color:var(--ink);font-weight:600;background:var(--white);border-top:2px solid var(--blue);width:130px}
.tab-panel{left:210px;top:609px;width:532px;height:53px;border:1px solid var(--line);padding:6px 27px}
.tab-panel h4{font-size:8px;font-weight:600;line-height:10px}
.tab-panel p{font-size:7px;line-height:10px;color:var(--muted)}
.quote{left:759px;top:598px;width:258px;height:58px;background:var(--panel);padding:8px 0 0 64px;font-size:6.8px;line-height:8px;color:var(--muted)}
.quote-mark{left:790px;top:600px;font-size:22px;color:#555;font-weight:700}
.quote-by{left:900px;top:656px;width:110px;text-align:right;font-size:8px;font-weight:600;line-height:9px}
.pager{top:577px;width:17px;height:7px;background:#ccc}
.date{width:36px;height:13px;background:#f0f0f0;border-radius:50%;font-size:5.5px;line-height:6px;text-align:center;color:#777;padding-top:1px}
.news h3{font-size:11px;font-weight:600;line-height:12px}
.news p{font-size:6.8px;line-height:8px;color:var(--muted);width:200px}
.footer{left:0;top:848px;width:1200px;height:137px;background:var(--footer);border-top:2px solid var(--blue)}
.footer-base{left:0;top:985px;width:1200px;height:15px;background:var(--footer-deep);color:var(--footer-text);font-size:6px;line-height:15px}
.about h3{font-size:19px;font-weight:400;color:var(--white);line-height:22px}
.about p{font-size:7px;line-height:8px;color:var(--footer-text);width:145px}
.about a{font-size:6px;color:var(--blue);text-decoration:none}
.archives h3{font-size:10px;font-weight:400;color:var(--white)}
.archives li{list-style:none;font-size:6.2px;color:var(--footer-text);height:12.2px;line-height:11px;border-bottom:1px solid #4a4a4a;width:185px}
.archives li::before{content:"›";margin-right:8px}
.social-label{font-size:6px;font-weight:700;color:var(--white);letter-spacing:.3px}
.social{width:26px;height:11px;border-radius:1px;top:957px}
</style>
</head>
<body>

<div class="abs topbar">
  <span style="left:212px"><i class="dot"></i>0000-0000-0000-0</span>
  <span style="left:338px"><i class="dot"></i>contact@verdanith-mail.com</span>
  <span style="left:498px"><i class="dot"></i>You Tag Lines Here</span>
  <i class="social-top" style="left:874px"></i>
  <i class="social-top" style="left:896px"></i>
  <i class="social-top" style="left:915px"></i>
  <i class="social-top" style="left:933px"></i>
  <i class="social-top" style="left:953px"></i>
  <i class="social-top" style="left:971px"></i>
  <i class="social-top" style="left:988px"></i>
  <i class="social-top" style="left:1006px"></i>
</div>

<header class="abs header"></header>
<div class="abs brand"><span class="brand-mark"></span><span class="brand-name">Verdanith</span></div>
<nav>
  <span class="abs nav active" style="left:456px">Home ▾</span>
  <span class="abs nav" style="left:547px">Portfolio ▾</span>
  <span class="abs nav" style="left:635px">Blog ▾</span>
  <span class="abs nav" style="left:701px">Pages ▾</span>
  <span class="abs nav" style="left:774px">Features ▾</span>
  <span class="abs nav" style="left:866px">Shortcodes ▾</span>
  <span class="abs nav" style="left:960px">Contact</span>
</nav>

<section class="abs hero" role="img" aria-label="Armed security team beside a dark pickup truck on a city street"></section>
<div class="abs hero-rule"></div>
<div class="abs hero-title">Lorem ipsum dolor sit amet, consectetur adipisicing elit</div>
<div class="abs hero-tag" style="top:102px">Lorem Ipsum is simply dummy text</div>
<div class="abs hero-tag" style="top:122px">Lorem Ipsum is simply lorem</div>
<div class="abs hero-tag" style="top:142px">Lorem Ipsum is simply</div>

<section class="abs intro">
  <h2>This is A Smart idea For Your Business</h2>
  <p>Lorem Ipsum is simply dummy text of the printing and typesetting industry</p>
</section>

<!-- features -->
<div class="abs feature-icon" style="left:209px;top:296px"></div>
<div class="abs feature" style="left:261px;top:294px"><h3>Lorem Ipsum</h3><p>Lorem Ipsum is simply dummy text of the printing and typesetting industry. Lorem Ipsum has been the industry's standard dummy text ever since the 1500s</p><a>Learn More</a></div>
<div class="abs feature-icon" style="left:483px;top:296px"></div>
<div class="abs feature" style="left:535px;top:294px"><h3>Lorem Ipsum</h3><p>Lorem Ipsum is simply dummy text of the printing and typesetting industry. Lorem Ipsum has been the industry's standard dummy text ever since the 1500s</p><a>Learn More</a></div>
<div class="abs feature-icon" style="left:757px;top:296px"></div>
<div class="abs feature" style="left:815px;top:294px"><h3>Lorem Ipsum</h3><p>Lorem Ipsum is simply dummy text of the printing and typesetting industry. Lorem Ipsum has been the industry's standard dummy text ever since the 1500s</p><a>Learn More</a></div>
<div class="abs feature-icon" style="left:209px;top:373px"></div>
<div class="abs feature" style="left:261px;top:371px"><h3>Lorem Ipsum</h3><p>Lorem Ipsum is simply dummy text of the printing and typesetting industry. Lorem Ipsum has been the industry's standard dummy text ever since the 1500s</p><a>Learn More</a></div>
<div class="abs feature-icon" style="left:483px;top:373px"></div>
<div class="abs feature" style="left:535px;top:371px"><h3>Lorem Ipsum</h3><p>Lorem Ipsum is simply dummy text of the printing and typesetting industry. Lorem Ipsum has been the industry's standard dummy text ever since the 1500s</p><a>Learn More</a></div>
<div class="abs feature-icon" style="left:757px;top:373px"></div>
<div class="abs feature" style="left:815px;top:371px"><h3>Lorem Ipsum</h3><p>Lorem Ipsum is simply dummy text of the printing and typesetting industry. Lorem Ipsum has been the industry's standard dummy text ever since the 1500s</p><a>Learn More</a></div>

<!-- our work -->
<h2 class="abs section-title" style="left:209px;top:460px">Our Work</h2>
<span class="abs section-link" style="left:929px;top:463px">View All Projects</span>
<div class="abs section-rule" style="left:209px;top:475px;width:807px"></div>
<div class="abs photo" style="left:210px;top:485px;width:189px;background:linear-gradient(135deg,#c9ccc7,#7b8a6a 55%,#2c2f35)" role="img" aria-label="Security officer in a reflective vest directing traffic"></div>
<div class="abs photo" style="left:416px;top:485px;width:189px;background:linear-gradient(135deg,#2a2218,#5b4632 50%,#1c1a18)" role="img" aria-label="Operator watching a wall of surveillance monitors"></div>
<div class="abs photo" style="left:622px;top:485px;width:189px;background:linear-gradient(160deg,#b9b5ae,#8b8a84 50%,#3a3c3f)" role="img" aria-label="Two guards in uniform walking down a street"></div>
<div class="abs photo" style="left:828px;top:485px;width:188px;background:linear-gradient(135deg,#4a4442,#8a7a70 45%,#2a2a2c)" role="img" aria-label="Officer holding a rifle during training"></div>

<!-- services -->
<h2 class="abs section-title" style="left:209px;top:572px">Our Services</h2>
<div class="abs section-rule" style="left:209px;top:587px;width:533px"></div>
<div class="abs tabs"><span class="tab on">Lorem Ipsum</span><span class="tab">Lorem Ipsum</span><span class="tab">Lorem Ipsum</span></div>
<div class="abs tab-panel">
  <h4>Lorem Ipsum is simply dummy text of the printing</h4>
  <p>Lorem Ipsum is simply dummy text of the printing and typesetting industry. Lorem Ipsum has been the industry's standard dummy text ever since the 1500s, when an unknown printer took a galley of type and scrambled it to make a type specimen book. It has survived not only five centuries, but also the leap into electronic typesetting, remaining essentially unchanged</p>
</div>

<h2 class="abs section-title" style="left:757px;top:572px">Testimonial</h2>
<div class="abs pager" style="left:979px"></div>
<div class="abs pager" style="left:998px"></div>
<div class="abs section-rule" style="left:757px;top:587px;width:259px"></div>
<div class="abs quote">Lorem Ipsum is simply dummy<br>text of the printing and typeset-<br>ting industry. Lorem Ipsum has<br>been the industry's standard<br>dummy text ever since the<br>1500s</div>
<div class="abs quote-mark">“</div>
<div class="abs quote-by">Lorem Ipsum<br>Li@Lorem Ipsum</div>

<!-- news -->
<h2 class="abs section-title" style="left:209px;top:681px">Recent News</h2>
<span class="abs section-link" style="left:942px;top:684px">Read The Blog</span>
<div class="abs section-rule" style="left:209px;top:696px;width:807px"></div>
<div class="abs" style="left:209px;top:705px;width:257px;height:55px;background:linear-gradient(180deg,#3b4a66,#8a8470 55%,#a79c80)" role="img" aria-label="Aircraft on a runway with ground crew"></div>
<div class="abs" style="left:483px;top:705px;width:257px;height:55px;background:linear-gradient(120deg,#c9c9c9,#4b4b4f 45%,#1f1f22 70%,#c8a640)" role="img" aria-label="Security vehicle with a guard at the door"></div>
<div class="abs" style="left:757px;top:705px;width:258px;height:55px;background:linear-gradient(180deg,#9a9d9f,#5d6164 50%,#8a8c8d)" role="img" aria-label="Rows of helmeted soldiers standing in formation"></div>
<div class="abs date" style="left:210px;top:766px">15<br>July</div>
<div class="abs news" style="left:259px;top:765px"><h3>Lorem Ipsum</h3><p>Lorem Ipsum is simply dummy text of the printing and typesetting industry. Lorem Ipsum has been the industry's standard dummy text ever since the 1500s</p></div>
<div class="abs date" style="left:484px;top:766px">15<br>July</div>
<div class="abs news" style="left:538px;top:765px"><h3>Lorem Ipsum</h3><p>Lorem Ipsum is simply dummy text of the printing and typesetting industry. Lorem Ipsum has been the industry's standard dummy text ever since the 1500s</p></div>
<div class="abs date" style="left:758px;top:766px">15<br>July</div>
<div class="abs news" style="left:817px;top:765px"><h3>Lorem Ipsum</h3><p>Lorem Ipsum is simply dummy text of the printing and typesetting industry. Lorem Ipsum has been the industry's standard dummy text ever since the 1500s</p></div>

<!-- footer -->
<footer class="abs footer"></footer>
<div class="abs about" style="left:208px;top:857px">
  <h3>About Us</h3>
  <p>Lorem Ipsum is simply dummy text of the printing and typesetting industry. Lorem Ipsum has been the industry's standard dummy text ever since the 1500s</p>
  <a style="display:block;margin-top:8px">READ MORE</a>
</div>
<div class="abs archives" style="left:417px;top:860px">
  <h3>Archives</h3>
  <ul>
    <li>January 2014</li><li>January 2014</li><li>January 2014</li><li>January 2014</li><li>January 2014</li><li>January 2014</li><li>January 2014</li>
  </ul>
</div>
<div class="abs" style="left:621px;top:877px;width:395px;height:63px;background:linear-gradient(135deg,#e4ddc8,#d6d2c2 50%,#e8e2cf)" role="img" aria-label="Street map showing the office location"></div>
<div class="abs social-label" style="left:621px;top:946px">SOCIAL ICON BY SHORTCODE</div>
<span class="abs social" style="left:622px;background:#3b5998"></span>
<span class="abs social" style="left:662px;background:#3fa9e0"></span>
<span class="abs social" style="left:702px;background:#e8e8e8"></span>
<span class="abs social" style="left:742px;background:#d9332b"></span>
<span class="abs social" style="left:782px;background:#2aa6dc"></span>
<span class="abs social" style="left:822px;background:#cc2127"></span>

<div class="abs footer-base">
  <span class="abs" style="left:217px">HOME &nbsp; | &nbsp; SUPPORT &nbsp; | &nbsp; SITE MAP &nbsp; | &nbsp; CONTACT</span>
  <span class="abs" style="left:792px">All rights reserved Verdanith Security, LLC...</span>
</div>

</body>
</html>
```